Business card for law firm

Need business card for new law firm. Think confident, authoritative, conservative, but not stuffy or old-fashioned.

Contact Information for Business Card

Content for card - logo (uploaded), plus the following:

Paul Whitcombe (larger font)
Managing Partner (larger font, but not as large as name)
Level 9, 7 Ferris Lane
Sydney NSW 2000
Main Tel 02 9364 2710
Direct Tel 02 8472 3159
Email paul@qvlegal.com.au
www.qvlegal.com.au

Letterhead design should include logo plus:
Level 9, 7 Ferris Lane
Sydney NSW 2000
Tel 02 8472 3159
www.qvlegal.com.au

```html
<!DOCTYPE html>
<html lang="en">
<head>
<meta charset="utf-8">
<title>Quayvale Legal – Business Card</title>
<link rel="stylesheet" href="https://fonts.googleapis.com/css2?family=Open+Sans:wght@400;600;700&display=swap">
<style>
  :root {
    --navy: #0b1f5c;
    --ink: #111111;
    --paper: #ffffff;
    --grey-text: #444444;
    --band-text: #e5e5e5;
    --backdrop: #e9eaec;
  }
  * { box-sizing: border-box; margin: 0; padding: 0; }
  html, body {
    width: 1200px; height: 960px; overflow: hidden;
    background: var(--backdrop);
    font-family: "Open Sans", Arial, sans-serif;
  }
  .sheet { position: relative; width: 1200px; height: 960px; }
  .card {
    position: absolute; left: 240px; width: 720px; height: 440px;
    background: var(--paper); overflow: hidden;
    box-shadow: 0 2px 10px rgba(0,0,0,0.12);
  }
  .card--brand { top: 30px; }
  .card--contact { top: 490px; }

  /* Brand side */
  .brand-square {
    position: absolute; left: 70px; top: 0; width: 200px; height: 300px;
    background: var(--navy);
  }
  .brand-lockup {
    position: absolute; left: 300px; top: 200px; width: 390px;
    text-align: center;
  }
  .brand-name {
    font-size: 36px; font-weight: 600; color: var(--ink);
    letter-spacing: 2px; text-transform: uppercase; white-space: nowrap;
    line-height: 1.2;
  }
  .brand-web {
    margin-top: 22px;
    font-size: 16px; color: var(--ink); letter-spacing: 3px;
  }

  /* Contact side */
  .mini-logo-square {
    position: absolute; left: 120px; top: 32px; width: 52px; height: 52px;
    background: var(--navy);
  }
  .mini-logo-name {
    position: absolute; left: 40px; top: 96px;
    font-size: 26px; font-weight: 600; color: var(--ink);
    letter-spacing: 1px; text-transform: uppercase; white-space: nowrap;
  }
  .name-band {
    position: absolute; left: 0; top: 160px; width: 410px; height: 95px;
    background: var(--ink); color: var(--paper);
    padding: 18px 0 0 40px;
  }
  .person-name {
    font-size: 21px; font-weight: 700; text-transform: uppercase; line-height: 1.15;
    white-space: nowrap;
  }
  .person-title {
    font-size: 14px; text-transform: uppercase; line-height: 1.5;
    white-space: nowrap;
  }
  .name-band .person-title { color: var(--band-text); }
  .address {
    position: absolute; left: 30px; top: 292px;
    font-size: 16px; color: var(--grey-text); white-space: nowrap;
  }
  .contact-panel {
    position: absolute; left: 380px; top: 212px; width: 340px; height: 160px;
    background: var(--navy);
  }
  .icon-column {
    position: absolute; left: 386px; top: 218px;
    display: flex; flex-direction: column; gap: 7px;
  }
  .icon { width: 20px; height: 20px; display: block; }
  .contact-list {
    position: absolute; left: 418px; top: 214px;
    list-style: none; color: var(--paper);
    font-size: 16px; line-height: 27px; white-space: nowrap;
  }
  .card-person { position: absolute; left: 470px; top: 130px; }
  .card-person .person-name { color: var(--navy); }
  .card-person .person-title { color: var(--ink); }
</style>
</head>
<body>
<main class="sheet">

  <section class="card card--brand" aria-label="Card front">
    <div class="brand-square"></div>
    <div class="brand-lockup">
      <p class="brand-name">Quayvale Legal</p>
      <p class="brand-web">www.qvlegal.com.au</p>
    </div>
  </section>

  <section class="card card--contact" aria-label="Card back">
    <div class="mini-logo-square"></div>
    <p class="mini-logo-name">Quayvale Legal</p>

    <div class="name-band">
      <p class="person-name">Paul Whitcombe</p>
      <p class="person-title">Managing Partner</p>
    </div>

    <p class="address">Level 9, 7 Ferris Lane, Sydney NSW 2000</p>

    <div class="contact-panel"></div>

    <div class="icon-column" aria-hidden="true">
      <svg class="icon" viewBox="0 0 20 20"><circle cx="10" cy="10" r="10" fill="#fff"/><path d="M7 5.5l2 2-1 1.3c.6 1.3 1.6 2.3 2.9 2.9l1.3-1 2 2-1.2 1.6c-3.5-.3-6.8-3.6-7.1-7.1z" fill="#111"/></svg>
      <svg class="icon" viewBox="0 0 20 20"><circle cx="10" cy="10" r="10" fill="#fff"/><path d="M7 5.5l2 2-1 1.3c.6 1.3 1.6 2.3 2.9 2.9l1.3-1 2 2-1.2 1.6c-3.5-.3-6.8-3.6-7.1-7.1z" fill="#111"/></svg>
      <svg class="icon" viewBox="0 0 20 20"><circle cx="10" cy="10" r="10" fill="#fff"/><rect x="5" y="6.5" width="10" height="7" fill="none" stroke="#111" stroke-width="1.3"/><path d="M5 6.5l5 4 5-4" fill="none" stroke="#111" stroke-width="1.3"/></svg>
      <svg class="icon" viewBox="0 0 20 20"><circle cx="10" cy="10" r="10" fill="#fff"/><circle cx="10" cy="10" r="5" fill="none" stroke="#111" stroke-width="1.2"/><ellipse cx="10" cy="10" rx="2.2" ry="5" fill="none" stroke="#111" stroke-width="1"/><path d="M5 10h10" stroke="#111" stroke-width="1"/></svg>
    </div>

    <ul class="contact-list">
      <li>02 9364 2710(Main)</li>
      <li>02 8472 3159(Direct)</li>
      <li>paul@qvlegal.com.au</li>
      <li>www.qvlegal.com.au</li>
    </ul>

    <div class="card-person">
      <p class="person-name">Paul Whitcombe</p>
      <p class="person-title">Managing Partner</p>
    </div>
  </section>

</main>
</body>
</html>
```